Cutting Edge Property Services Provider is Looking to Update Business Card Design

We are looking to freshen up our business cards to match our cutting edge technology based image.

KORVANEX - Where Care Finds Its Pulse

More information about our company can be found on our website at www.korvanex-demo.net

We integrate technology in a historically low tech industry.

We have appeared on the Brisk 300/3000 list 2 years in a row and we're previously recognized as the 5th Quickest Rising Firm in San Diego.

Our core colors are blue and white, but are not against accents that might improve our image.

We currently have our Mission Statement on our Business Cards in a folding design:
KORVANEX IS THE LEADING BUILDING SERVICES INNOVATOR. BY COMBINING TECHNOLOGY WITH FUNCTIONAL TOOS THAT IMPROVE EFFICIENCY IN THE WORKPLACE, WE PROVIDE UNPARALLELED SERVICE IN THE INDUSTRY. DEVELOPING LASTING RELATIONSHIPS WITH OUR CLIENTS AND ASSOCIATES IS THE CORNERSTONE OF OUR SUCCESS.

We'd like to convey the image of a cutting edge, technology based company. Want the cards to pop.

Target Market(s)

Commercial Property Managers - 20 to 50 year old professionals

Industry/Entity Type

Business

Requirements
Must have
• Must utilize our logo obviously, but are definitely open to using variations on the logo. Utilizing the components of the logo, but maybe in different configurations or backgrounds, etc...

Must use the Name: KORVANEX.
Can also use KORVANEX PROPERTY SERVICES.

Must include the Mission Statement

Must say: Where Care Finds Its Pulse
Nice to have
• We are considering plastic stock, shaped cards, or folding cards.

Nothing over the top or really expensive, but will consider if it conveys innovation and technology.
Should not have
• No images of toilets, buildings, trees, or anything relating to commercial properties.

We want to convey our technology image.

```html
<!DOCTYPE html>
<html lang="en">
<head>
<meta charset="utf-8">
<title>KORVANEX business card, front and back</title>
<link rel="stylesheet" href="https://fonts.googleapis.com/css2?family=Saira:wght@400;700&family=Open+Sans:wght@600&display=swap">
<style>
  :root {
    --page: #ebe8e3;
    --stock-light: #d2b696;
    --stock-dark: #bf9c78;
    --brand-blue: #0f4c81;
    --band-blue: #155891;
    --silver-light: #f1f2f4;
    --silver-dark: #a9adb3;
    --ink-blue: #1b4f86;
    --tagline: #2a4f78;
    --white: #ffffff;
  }
  * { margin: 0; padding: 0; box-sizing: border-box; }
  html, body { width: 1200px; height: 441px; overflow: hidden; background: var(--page); }
  .canvas { position: relative; width: 1200px; height: 441px; }

  .card {
    position: absolute; top: 92px; width: 343px; height: 194px;
    border-radius: 8px; overflow: hidden;
    background: linear-gradient(180deg, var(--stock-light), var(--stock-dark));
    box-shadow: 0 2px 6px rgba(0,0,0,.18);
  }
  .card--front { left: 241px; }
  .card--back { left: 621px; }
  .card-art { position: absolute; inset: 0; }

  .brand { position: absolute; top: 10px; left: 0; width: 100%; text-align: center; }
  .brand-mark {
    display: block; width: 66px; height: 66px; margin: 0 auto;
    background: var(--brand-blue); border-radius: 8px;
  }
  .brand-name {
    display: block; margin-top: 8px;
    font-family: "Saira", sans-serif; font-weight: 700; font-size: 20px;
    letter-spacing: 1.5px; line-height: 1; color: var(--brand-blue);
  }
  .brand-tagline {
    display: block; margin-top: 3px;
    font-family: "Saira", sans-serif; font-weight: 400; font-size: 9.5px;
    color: var(--tagline); line-height: 1;
  }
  .brand--reversed { transform: scaleX(-1); }
  .brand--reversed .brand-name { color: var(--ink-blue); }
  .brand--reversed .brand-tagline { color: #9a8f86; }

  .contact {
    position: absolute; top: 147px; left: 0; width: 100%;
    font-family: "Saira", sans-serif; font-size: 10px; line-height: 13.5px; color: var(--white);
  }
  .contact-address { position: absolute; right: 170px; text-align: right; white-space: nowrap; }
  .contact-divider { position: absolute; left: 180px; top: 1px; width: 1px; height: 39px; background: rgba(255,255,255,.7); }
  .contact-lines { position: absolute; left: 186px; list-style: none; white-space: nowrap; }
  .contact-lines li { display: flex; align-items: center; gap: 4px; }
  .contact-lines svg { width: 7px; height: 7px; fill: var(--white); flex: none; }

  .mission {
    position: absolute; top: 146px; left: 10px; right: 10px;
    font-family: "Open Sans", sans-serif; font-weight: 600; font-size: 6.4px;
    line-height: 9.6px; text-align: center; color: var(--white); text-transform: uppercase;
  }
</style>
</head>
<body>
<main class="canvas">

  <section class="card card--front" aria-label="Card front">
    <svg class="card-art" viewBox="0 0 343 194" aria-hidden="true">
      <defs>
        <linearGradient id="silverFront" x1="0" y1="0" x2="1" y2="0">
          <stop offset="0" stop-color="var(--silver-dark)"/>
          <stop offset=".5" stop-color="var(--silver-light)"/>
          <stop offset="1" stop-color="var(--silver-dark)"/>
        </linearGradient>
      </defs>
      <path d="M0,120 Q120,110 343,113 L343,121 Q120,118 0,127 Z" fill="url(#silverFront)"/>
      <path d="M0,127 Q120,118 343,121 L343,194 L0,194 Z" fill="var(--band-blue)"/>
      <path d="M227,119 L239,119 L233,126 Z" fill="url(#silverFront)"/>
    </svg>
    <div class="brand">
      <span class="brand-mark"></span>
      <span class="brand-name">KORVANEX</span>
      <span class="brand-tagline">Where Care Finds Its Pulse</span>
    </div>
    <div class="contact">
      <p class="contact-address">2815 Linden Crest Way<br>Suite 210<br>San Diego, CA 92108</p>
      <span class="contact-divider"></span>
      <ul class="contact-lines">
        <li><svg viewBox="0 0 10 10"><path d="M2 0.5 L4 2.8 L3 4 Q4.3 6 6 7 L7.2 6 L9.5 8 L8.2 9.5 Q3.5 9 0.5 1.8 Z"/></svg>1(800) 555-0142</li>
        <li><svg viewBox="0 0 10 10"><path d="M0.5 2 H9.5 V8.5 H0.5 Z M1 2.5 L5 5.5 L9 2.5" stroke="#155891" stroke-width=".8"/></svg>info@korvanex-demo.net</li>
        <li><svg viewBox="0 0 10 10"><circle cx="5" cy="5" r="4.5"/><path d="M0.5 5 H9.5 M5 0.5 V9.5 M5 0.5 Q2 5 5 9.5 M5 0.5 Q8 5 5 9.5" stroke="#155891" stroke-width=".7" fill="none"/></svg>www.korvanex-demo.net</li>
      </ul>
    </div>
  </section>

  <section class="card card--back" aria-label="Card back">
    <svg class="card-art" viewBox="0 0 343 194" aria-hidden="true">
      <defs>
        <linearGradient id="silverBack" x1="0" y1="0" x2="1" y2="0">
          <stop offset="0" stop-color="var(--silver-dark)"/>
          <stop offset=".5" stop-color="var(--silver-light)"/>
          <stop offset="1" stop-color="var(--silver-dark)"/>
        </linearGradient>
      </defs>
      <path d="M0,113 Q223,110 343,120 L343,127 Q223,118 0,121 Z" fill="url(#silverBack)"/>
      <path d="M0,121 Q223,118 343,127 L343,194 L0,194 Z" fill="var(--band-blue)"/>
      <path d="M104,119 L116,119 L110,126 Z" fill="url(#silverBack)"/>
    </svg>
    <div class="brand brand--reversed">
      <span class="brand-mark"></span>
      <span class="brand-name">KORVANEX</span>
      <span class="brand-tagline">Where Care Finds Its Pulse</span>
    </div>
    <p class="mission">KORVANEX is the leading building services innovator. By combining technology<br>with functional toos that improve efficiency in the workplace, we provide<br>unparalleled service in the industry. Developing lasting relationships with<br>our clients and associates is the cornerstone of our success.</p>
  </section>

</main>
</body>
</html>
```